Wealth Education Business Needs Sharp Business Card Design

We need a business card design for a recently launched investor education business called Harbor Crest.

The final design should promote security, empowerment, self improvement and financial gain. The card will ideally promote the stature of the business.

For more information and colours please visit harborcrest.com.au

Target Market(s)

Corporate executives and high net worth individuals

Industry/Entity Type

Education

Contact Information for Business Card

```html
<!DOCTYPE html>
<html lang="en">
<head>
<meta charset="utf-8">
<title>Harbor Crest – Business Card</title>
<link rel="stylesheet" href="https://fonts.googleapis.com/css2?family=Oswald:wght@500;600&family=Open+Sans:wght@400;700&display=swap">
<style>
  :root {
    --navy: #1c2a3d;
    --white: #ffffff;
    --teal: #2aa39a;
    --muted: #6f7e90;
    --light-text: #e6ebf1;
    --stage: #e9ebee;
  }
  * { box-sizing: border-box; margin: 0; padding: 0; }
  html, body {
    width: 1200px; height: 902px; overflow: hidden;
    background: var(--stage);
  }
  .stage {
    position: relative; width: 1200px; height: 902px;
    display: flex; align-items: center; justify-content: center; gap: 60px;
  }
  .card {
    position: relative; width: 520px; height: 300px;
    border-radius: 14px; overflow: hidden;
    box-shadow: 0 6px 18px rgba(0,0,0,.18);
  }

  /* Front */
  .card-front { background: var(--navy); }
  .front-lockup {
    position: absolute; left: 0; right: 0; top: 96px; text-align: center;
  }
  .brand-name {
    font-family: "Oswald", sans-serif; font-weight: 600;
    letter-spacing: 3px; text-transform: uppercase; white-space: nowrap;
  }
  .card-front .brand-name { color: var(--white); font-size: 40px; line-height: 1; }
  .tagline {
    margin-top: 10px;
    font-family: "Oswald", sans-serif; font-weight: 500;
    color: var(--teal); font-size: 14px; letter-spacing: 6px; text-transform: uppercase;
  }
  .front-web {
    position: absolute; left: 0; right: 0; bottom: 58px; text-align: center;
    font-family: "Open Sans", sans-serif; font-size: 12px; color: var(--muted);
  }

  /* Back */
  .card-back { background: var(--white); }
  .back-band { position: absolute; inset: 0; }
  .back-brand {
    position: absolute; left: 0; right: 0; top: 52px;
    display: flex; align-items: center; justify-content: center; gap: 14px;
  }
  .card-back .brand-name { color: var(--navy); font-size: 36px; line-height: 1; }
  .brand-dot { width: 14px; height: 14px; border-radius: 50%; background: var(--teal); }

  .person {
    position: absolute; left: 28px; top: 188px; width: 220px; text-align: right;
    font-family: "Open Sans", sans-serif; color: var(--light-text);
  }
  .person-name { font-weight: 700; font-size: 17px; text-transform: uppercase; color: var(--white); }
  .person-title { font-size: 11px; margin-top: 1px; }
  .person-address { font-size: 12px; margin-top: 12px; line-height: 1.45; }

  .divider {
    position: absolute; left: 266px; top: 182px; width: 1px; height: 96px;
    background: rgba(255,255,255,.35);
  }
  .contacts {
    position: absolute; left: 284px; top: 178px; list-style: none;
    font-family: "Open Sans", sans-serif; font-size: 12px; color: var(--light-text);
  }
  .contacts li { display: flex; align-items: center; gap: 9px; height: 25px; white-space: nowrap; }
  .contacts svg { width: 12px; height: 12px; fill: var(--white); flex: none; }
</style>
</head>
<body>
<main class="stage">

  <section class="card card-front" aria-label="Card front">
    <div class="front-lockup">
      <div class="brand-name">Harbor Crest</div>
      <div class="tagline">Study Plan Flourish</div>
    </div>
    <div class="front-web">www.harborcrest.com.au</div>
  </section>

  <section class="card card-back" aria-label="Card back">
    <svg class="back-band" viewBox="0 0 520 300" preserveAspectRatio="none" aria-hidden="true">
      <path d="M0 168 Q 260 158 520 100 L520 300 L0 300 Z" fill="var(--navy)"/>
    </svg>

    <div class="back-brand">
      <span class="brand-dot"></span>
      <span class="brand-name">Harbor Crest</span>
    </div>

    <div class="person">
      <div class="person-name">Your Name</div>
      <div class="person-title">Title</div>
      <div class="person-address">Level 2, 48 Quayside Row<br>Southbank VIC 3006</div>
    </div>

    <div class="divider"></div>

    <ul class="contacts">
      <li>
        <svg viewBox="0 0 24 24" aria-hidden="true"><path d="M6.6 10.8a15.1 15.1 0 0 0 6.6 6.6l2.2-2.2a1 1 0 0 1 1-.25 11.4 11.4 0 0 0 3.6.57 1 1 0 0 1 1 1V20a1 1 0 0 1-1 1A17 17 0 0 1 3 4a1 1 0 0 1 1-1h3.5a1 1 0 0 1 1 1c0 1.250.2 2.450.57 3.570a1 1 0 0 1-.25 1z"/></svg>
        1300 555 014
      </li>
      <li>
        <svg viewBox="0 0 24 24" aria-hidden="true"><path d="M6 2h9l3 3v4H6zM4 10h16a2 2 0 0 1 2 2v6h-4v4H6v-4H2v-6a2 2 0 0 1 2-2zm4 6v4h8v-4z"/></svg>
        +613 5550 1942
      </li>
      <li>
        <svg viewBox="0 0 24 24" aria-hidden="true"><path d="M2 5h20v14H2zm2 2v.5l8 5 8-5V7l-8 5z"/></svg>
        support@harborcrest.com.au
      </li>
      <li>
        <svg viewBox="0 0 24 24" aria-hidden="true"><path d="M12 2a10 10 0 1 0 0 20 10 10 0 0 0 0-20zm6.9 9h-3a15 15 0 0 0-1.3-5.6A8 8 0 0 1 18.9 11zM12 4.1c.9 1.2 1.8 3.6 1.9 6.9h-3.8c.1-3.3 1-5.7 1.9-6.9zM9.4 5.4A15 15 0 0 0 8.1 11h-3a8 8 0 0 1 4.3-5.6zM5.1 13h3a15 15 0 0 0 1.3 5.6A8 8 0 0 1 5.1 13zm6.9 6.9c-.9-1.2-1.8-3.6-1.9-6.9h3.8c-.1 3.3-1 5.7-1.9 6.9zm2.6-1.3a15 15 0 0 0 1.3-5.6h3a8 8 0 0 1-4.3 5.6z"/></svg>
        www.harborcrest.com.au
      </li>
    </ul>
  </section>

</main>
</body>
</html>
```